Hair and Wellness Brochure and Pricelist design

I am requiring a brochure that has a fresh, though alternative design. My business name is The Quiet Orchard Hair and Wellness. I have a very professional approach to my work and love to give that little bit extra to all of my clients. My passion for health, has led me to channel my business alternatively by using non toxic colours and styling products and through that same vein, I have studied Aromatherapy, Indian Head Massage and Reiki...all additional services I use where required.
My studio has very neutral tones of beige,white and beech wood but these tones aren't necessarily required for the brochure.I like to create a space of calm, peace and quiet, where my clients feel refreshed and rejuvenated..

Industry/Entity Type

Business

```html
<!DOCTYPE html>
<html lang="en">
<head>
<meta charset="utf-8">
<title>The Quiet Orchard Hair and Wellness – Brochure</title>
<link rel="stylesheet" href="https://fonts.googleapis.com/css2?family=Barlow+Semi+Condensed:wght@600;700&family=Barlow:wght@600;700&display=swap">
<style>
  :root {
    --page: #ffffff;
    --wood-light: #dcae97;
    --wood-mid: #cf9d86;
    --wood-dark: #c4907a;
    --ribbon-a: #97c93d;
    --ribbon-b: #66a33f;
    --ink: #2b1c18;
    --white: #ffffff;
    --band: rgba(245, 232, 226, 0.7);
    --fold: rgba(60, 40, 35, 0.55);
  }
  * { box-sizing: border-box; margin: 0; padding: 0; }
  html, body { width: 1200px; height: 1000px; overflow: hidden; background: var(--page); }
  body { position: relative; font-family: "Barlow Semi Condensed", "Arial Narrow", sans-serif; color: var(--ink); }

  .brochure { position: absolute; left: 117px; top: 125px; width: 966px; height: 750px; overflow: hidden; }
  .wood {
    position: absolute; inset: 0;
    background:
      linear-gradient(180deg, rgba(255,255,255,0.05) 0 12%, rgba(0,0,0,0.03) 12% 25%, rgba(255,255,255,0.05) 25% 40%, rgba(0,0,0,0.03) 40% 58%, rgba(255,255,255,0.05) 58% 75%, rgba(0,0,0,0.03) 75% 100%),
      linear-gradient(90deg, var(--wood-mid), var(--wood-light) 40%, var(--wood-mid) 70%, var(--wood-dark));
  }

  .fold { position: absolute; top: 0; bottom: 0; border-left: 1px dashed var(--fold); }
  .fold--one { left: 321px; }
  .fold--two { left: 641px; }

  .band-chevron { position: absolute; top: 111px; height: 40px; }

  .ribbon { position: absolute; top: 111px; width: 228px; height: 40px; filter: drop-shadow(0 2px 3px rgba(70,40,30,0.45)); }
  .ribbon svg { display: block; }
  .ribbon__label {
    position: absolute; inset: 0; display: flex; align-items: center; justify-content: center;
    color: var(--white); font-family: "Barlow", sans-serif; font-weight: 700; font-size: 20px; letter-spacing: 0.3px;
  }
  .ribbon--welcome { left: 43px; }
  .ribbon--contact { left: 363px; }

  .welcome-copy { position: absolute; left: 43px; top: 189px; width: 235px; font-weight: 700; font-size: 12px; line-height: 15.2px; white-space: nowrap; }
  .welcome-copy p + p { margin-top: 4px; }

  .contact { position: absolute; left: 328px; width: 300px; top: 234px; text-align: center; font-weight: 700; }
  .contact__business { font-size: 15px; line-height: 18px; }
  .contact__person { margin-top: 6px; font-size: 15px; line-height: 17.5px; }
  .contact__social { margin-top: 23px; font-size: 14.5px; }
  .contact__social-icon { display: block; margin: 8px auto 0; width: 46px; height: 46px; border-radius: 7px; background: var(--ribbon-b); box-shadow: 0 1px 3px rgba(0,0,0,0.3); }

  .brand-seal {
    position: absolute; border-radius: 50%;
    background: linear-gradient(90deg, var(--ribbon-a), var(--ribbon-b));
    color: var(--white); font-family: "Barlow", sans-serif; font-weight: 700; text-align: center;
    box-shadow: 0 2px 6px rgba(70,40,30,0.4);
  }
  .brand-seal__line { position: absolute; left: 0; right: 0; }
  .brand-seal--cover { left: 679px; top: 96px; width: 250px; height: 250px; font-size: 18px; }
  .brand-seal--cover .brand-seal__line--name { top: 52px; }
  .brand-seal--cover .brand-seal__line--trade { top: 176px; }
  .brand-seal--back { left: 390px; top: 506px; width: 184px; height: 184px; font-size: 14px; }
  .brand-seal--back .brand-seal__line--name { top: 38px; }
  .brand-seal--back .brand-seal__line--trade { top: 128px; }

  .tagline { position: absolute; left: 761px; top: 372px; font-weight: 700; font-size: 12.5px; line-height: 15px; }
</style>
</head>
<body>
  <main class="brochure">
    <div class="wood" role="img" aria-label="Light beech wood plank texture background"></div>

    <div class="fold fold--one"></div>
    <div class="fold fold--two"></div>

    <svg class="band-chevron" style="left:0;width:36px" viewBox="0 0 36 40"><polygon points="0,0 28,0 36,20 28,40 0,40" fill="var(--band)"/></svg>
    <svg class="band-chevron" style="left:279px;width:76px" viewBox="0 0 76 40"><polygon points="8,0 68,0 76,20 68,40 8,40 0,20" fill="var(--band)"/></svg>
    <svg class="band-chevron" style="left:600px;width:366px" viewBox="0 0 366 40"><polygon points="8,0 366,0 366,40 8,40 0,20" fill="var(--band)"/></svg>

    <div class="ribbon ribbon--welcome">
      <svg width="228" height="40" viewBox="0 0 228 40">
        <defs><linearGradient id="ribbonFill" x1="0" x2="1"><stop offset="0" stop-color="var(--ribbon-a)"/><stop offset="1" stop-color="var(--ribbon-b)"/></linearGradient></defs>
        <polygon points="0,0 228,0 222,20 228,40 0,40 6,20" fill="url(#ribbonFill)"/>
        <line x1="8" y1="4" x2="220" y2="4" stroke="#fff" stroke-width="1" stroke-dasharray="3 2"/>
        <line x1="8" y1="36" x2="220" y2="36" stroke="#fff" stroke-width="1" stroke-dasharray="3 2"/>
      </svg>
      <span class="ribbon__label">WELCOME</span>
    </div>
    <div class="ribbon ribbon--contact">
      <svg width="228" height="40" viewBox="0 0 228 40">
        <polygon points="0,0 228,0 222,20 228,40 0,40 6,20" fill="url(#ribbonFill)"/>
        <line x1="8" y1="4" x2="220" y2="4" stroke="#fff" stroke-width="1" stroke-dasharray="3 2"/>
        <line x1="8" y1="36" x2="220" y2="36" stroke="#fff" stroke-width="1" stroke-dasharray="3 2"/>
      </svg>
      <span class="ribbon__label">CONTACT</span>
    </div>

    <section class="welcome-copy">
      <p>Here at The Quiet Orchard Hair<br>and Wellness, we specialise in all<br>professional hairdressing services<br>including corrective colour services<br>and wedding up styles.</p>
      <p>Mara, the solo hair stylist working out<br>of a beautiful home studio, has over 20<br>years experience in the industry with an<br>education obtained at the prestigious<br>Hartwell Academy in London.</p>
      <p>With a focus on health, we pride<br>ourselves on using non toxic colours and<br>styling products so you’ll never have to<br>worry about harsh chemicals damaging<br>your hair or your skin.</p>
    </section>

    <section class="contact">
      <p class="contact__business">The Quiet Orchard<br>Hair and Wellness</p>
      <p class="contact__person">Mara Ellison<br>0400 555 018<br>mara@quietorchard.com</p>
      <p class="contact__social">LIKE US on Chatterbox</p>
      <span class="contact__social-icon"></span>
    </section>

    <div class="brand-seal brand-seal--back">
      <span class="brand-seal__line brand-seal__line--name">THE QUIET ORCHARD</span>
      <span class="brand-seal__line brand-seal__line--trade">HAIR &amp; WELLNESS</span>
    </div>
    <div class="brand-seal brand-seal--cover">
      <span class="brand-seal__line brand-seal__line--name">THE QUIET ORCHARD</span>
      <span class="brand-seal__line brand-seal__line--trade">HAIR &amp; WELLNESS</span>
    </div>

    <p class="tagline">PROFESSIONAL<br>HAIRDRESSING</p>
  </main>
</body>
</html>
```